FinTech company looking to revamp and expand client-facing interface for our financial models

Pellworth Engines currently has a very simple website that allows clients to interact with our financial models. We are looking to completely redesign the current site and add several extra pages to provide extra functionality. We want the design to have a modern, slick feel, that will work on both a desktop or a tablet. It should be straightforward for clients to move between different pages at any time, and clear from the layout how to interact with the more advanced features. We have included screenshots of existing pages in the attached design brief, as well as sketches of the functionality required by the new pages, but can't provide a direct link to the current site.
Target Market(s)
Professional investors that will be paying to access the interface
Industry/Entity Type
Finance
Number of Pages Required
4 page
Colors
Designer to choose colors to be used in the design.
Look and feel
Each slider illustrates characteristics of the customer's brand and the style your logo design should communicate.

```html
<!DOCTYPE html>
<html lang="en">
<head>
<meta charset="utf-8">
<title>Quorin · Models</title>
<link href="https://fonts.googleapis.com/css2?family=Montserrat:wght@400;500;600&display=swap" rel="stylesheet">
<style>
:root{
  --bg:#e7eef5;
  --white:#ffffff;
  --row-alt:#f4f8fc;
  --ink:#22252b;
  --muted:#8a939e;
  --accent:#2b86e3;
  --accent-soft:#9cc4ee;
  --divider:#cfe0f2;
  --star-on:#ec4b4b;
  --star-off:#b9bec6;
}
*{margin:0;padding:0;box-sizing:border-box}
html,body{width:1200px;height:746px;overflow:hidden}
body{font-family:'Montserrat',sans-serif;background:var(--bg);color:var(--ink);position:relative}
.topbar{position:absolute;left:0;top:0;width:1200px;height:67px;background:var(--white);box-shadow:0 4px 16px rgba(60,100,150,.06)}
.brand{position:absolute;left:150px;top:18px;font-size:23px;font-weight:600;letter-spacing:.5px;color:var(--ink)}
.nav-item{position:absolute;top:0;height:67px;display:flex;align-items:center;gap:6px;font-size:13px;color:var(--ink)}
.nav-item.active{color:var(--accent)}
.nav-item.active::after{content:"";position:absolute;bottom:0;height:2px;background:var(--accent);left:var(--ul,-8px);right:var(--ur,-8px)}
.nav-item svg{width:14px;height:14px;stroke:currentColor;fill:none;stroke-width:1.6}
.tabs{position:absolute;left:150px;top:118px;width:900px;height:52px;background:var(--white);border-radius:3px}
.tab{position:absolute;top:0;height:52px;line-height:52px;font-size:11px;letter-spacing:.5px;color:var(--ink)}
.tab.active{color:var(--accent)}
.tab.active::after{content:"";position:absolute;left:-7px;right:-8px;bottom:0;height:2px;background:var(--accent)}
.tab.add{color:var(--accent-soft);font-size:12px;letter-spacing:0}
.tab-sep{position:absolute;top:15px;height:22px;border-left:1px dashed var(--divider)}
.tool{position:absolute;top:198px;display:flex;align-items:center;gap:6px;font-size:13px;color:var(--accent)}
.tool svg{width:13px;height:13px;stroke:currentColor;fill:none;stroke-width:1.6}
.table{position:absolute;left:150px;top:226px;width:900px;height:464px;border-radius:4px;overflow:hidden;background:var(--white)}
.row{position:relative;height:70px;font-size:13px}
.row:nth-child(odd){background:var(--row-alt)}
.row.head{height:46px;background:var(--row-alt);color:var(--muted)}
.row.head + .row{background:var(--white)}
.row.head + .row + .row{background:var(--row-alt)}
.row.head + .row + .row + .row{background:var(--white)}
.row.head + .row + .row + .row + .row{background:var(--row-alt)}
.row.head + .row + .row + .row + .row + .row{background:var(--white)}
.row.head + .row + .row + .row + .row + .row + .row{background:var(--row-alt)}
.cell{position:absolute;top:50%;transform:translateY(-50%);white-space:nowrap;line-height:16px}
.star{position:absolute;left:10px;top:50%;transform:translateY(-50%);width:9px;height:9px}
.star path{fill:none;stroke:var(--star-off);stroke-width:1.2}
.star.on path{fill:var(--star-on);stroke:var(--star-on)}
</style>
</head>
<body>
<header class="topbar">
  <div class="brand">Quorin</div>
  <div class="nav-item active" style="left:276px">250D</div>
  <div class="nav-item" style="left:340px">83D</div>
  <div class="nav-item" style="left:397px">42D</div>
  <div class="nav-item active" style="left:553px;--ul:-15px;--ur:-14px">
    <svg viewBox="0 0 16 16"><path d="M2 8 8 2.5 14 8M4 6.5V14h8V6.5"/></svg>Models</div>
  <div class="nav-item" style="left:661px">
    <svg viewBox="0 0 16 16"><circle cx="3" cy="3" r="1.3"/><circle cx="8" cy="3" r="1.3"/><circle cx="13" cy="3" r="1.3"/><circle cx="3" cy="8" r="1.3"/><circle cx="8" cy="8" r="1.3"/><circle cx="13" cy="8" r="1.3"/><circle cx="3" cy="13" r="1.3"/><circle cx="8" cy="13" r="1.3"/></svg>Portfolio Builder</div>
  <div class="nav-item" style="left:820px">
    <svg viewBox="0 0 16 16"><path d="M8 2 15 6 8 10 1 6Z M1 9.5 8 13.5 15 9.5"/></svg>Sensitivities</div>
  <div class="nav-item" style="left:958px">
    <svg viewBox="0 0 16 16"><path d="M8 1.5 10 6h4.7l-3.8 3 1.4 4.8L8 11l-4.3 2.8L5.1 9 1.3 6H6Z"/></svg>Favourites</div>
</header>

<nav class="tabs">
  <div class="tab active" style="left:26px">EQUITIES</div>
  <div class="tab-sep" style="left:101px"></div>
  <div class="tab" style="left:122px">ETFS</div>
  <div class="tab-sep" style="left:174px"></div>
  <div class="tab" style="left:193px">PAIRS</div>
  <div class="tab-sep" style="left:249px"></div>
  <div class="tab" style="left:270px">ETF PAIRS</div>
  <div class="tab-sep" style="left:351px"></div>
  <div class="tab" style="left:371px">FACTORS</div>
  <div class="tab add" style="left:447px">+ Add</div>
</nav>

<div class="tool" style="left:150px">
  <svg viewBox="0 0 14 14"><path d="M1 1.5h12L8.3 7.3v5L5.7 11V7.3Z"/></svg>Filter</div>
<div class="tool" style="right:150px">
  <svg viewBox="0 0 14 14"><path d="M11 8v4.5H1.5V3H6M8.5 1.5h4v4M12.5 1.5 6.5 7.5"/></svg>Export</div>

<section class="table">
  <div class="row head">
    <div class="cell" style="left:14px">ID&#8964;</div>
    <div class="cell" style="left:90px">Sector</div>
    <div class="cell" style="left:173px">Time</div>
    <div class="cell" style="left:260px">Quality</div>
    <div class="cell" style="left:340px">Stat 1</div>
    <div class="cell" style="left:409px">Stat 2</div>
    <div class="cell" style="left:480px">Stat 3</div>
    <div class="cell" style="left:551px">Stat 4</div>
    <div class="cell" style="left:624px">Stat 5</div>
    <div class="cell" style="left:695px">Stat 6</div>
    <div class="cell" style="left:766px">Stat 7</div>
    <div class="cell" style="left:838px">Stat 8</div>
  </div>
  <div class="row">
    <svg class="star" viewBox="0 0 10 10"><path d="M5 .8 6.2 3.7H9.3L6.8 5.6 7.7 8.8 5 7 2.3 8.8 3.2 5.6.7 3.7H3.8Z"/></svg>
    <div class="cell" style="left:25px">Model 1</div><div class="cell" style="left:92px">Materials</div>
    <div class="cell" style="left:175px">2019-07-03<br>12:15:00.000</div>
    <div class="cell" style="left:263px">30.2888</div><div class="cell" style="left:341px">2.01574</div>
    <div class="cell" style="left:410px">23.305</div><div class="cell" style="left:478px">-0.149368</div>
    <div class="cell" style="left:552px">22.3054</div><div class="cell" style="left:624px">4.63714</div>
    <div class="cell" style="left:696px">0.945706</div><div class="cell" style="left:766px">2.81949</div>
    <div class="cell" style="left:833px">2.60858</div>
  </div>
  <div class="row">
    <svg class="star on" viewBox="0 0 10 10"><path d="M5 .8 6.2 3.7H9.3L6.8 5.6 7.7 8.8 5 7 2.3 8.8 3.2 5.6.7 3.7H3.8Z"/></svg>
    <div class="cell" style="left:25px">Model 2</div><div class="cell" style="left:92px">Materials</div>
    <div class="cell" style="left:175px">2019-07-03<br>12:15:00.000</div>
    <div class="cell" style="left:263px">30.2888</div><div class="cell" style="left:341px">2.01574</div>
    <div class="cell" style="left:410px">23.305</div><div class="cell" style="left:478px">-0.149368</div>
    <div class="cell" style="left:552px">22.3054</div><div class="cell" style="left:624px">4.63714</div>
    <div class="cell" style="left:696px">0.945706</div><div class="cell" style="left:766px">2.81949</div>
    <div class="cell" style="left:833px">2.60858</div>
  </div>
  <div class="row">
    <svg class="star" viewBox="0 0 10 10"><path d="M5 .8 6.2 3.7H9.3L6.8 5.6 7.7 8.8 5 7 2.3 8.8 3.2 5.6.7 3.7H3.8Z"/></svg>
    <div class="cell" style="left:25px">Model 3</div><div class="cell" style="left:92px">Materials</div>
    <div class="cell" style="left:175px">2019-07-03<br>12:15:00.000</div>
    <div class="cell" style="left:263px">30.2888</div><div class="cell" style="left:341px">2.01574</div>
    <div class="cell" style="left:410px">23.305</div><div class="cell" style="left:478px">-0.149368</div>
    <div class="cell" style="left:552px">22.3054</div><div class="cell" style="left:624px">4.63714</div>
    <div class="cell" style="left:696px">0.945706</div><div class="cell" style="left:766px">2.81949</div>
    <div class="cell" style="left:833px">2.60858</div>
  </div>
  <div class="row">
    <svg class="star" viewBox="0 0 10 10"><path d="M5 .8 6.2 3.7H9.3L6.8 5.6 7.7 8.8 5 7 2.3 8.8 3.2 5.6.7 3.7H3.8Z"/></svg>
    <div class="cell" style="left:25px">Model 4</div><div class="cell" style="left:92px">Materials</div>
    <div class="cell" style="left:175px">2019-07-03<br>12:15:00.000</div>
    <div class="cell" style="left:263px">30.2888</div><div class="cell" style="left:341px">2.01574</div>
    <div class="cell" style="left:410px">23.305</div><div class="cell" style="left:478px">-0.149368</div>
    <div class="cell" style="left:552px">22.3054</div><div class="cell" style="left:624px">4.63714</div>
    <div class="cell" style="left:696px">0.945706</div><div class="cell" style="left:766px">2.81949</div>
    <div class="cell" style="left:833px">2.60858</div>
  </div>
  <div class="row">
    <svg class="star" viewBox="0 0 10 10"><path d="M5 .8 6.2 3.7H9.3L6.8 5.6 7.7 8.8 5 7 2.3 8.8 3.2 5.6.7 3.7H3.8Z"/></svg>
    <div class="cell" style="left:25px">Model 5</div><div class="cell" style="left:92px">Materials</div>
    <div class="cell" style="left:175px">2019-07-03<br>12:15:00.000</div>
    <div class="cell" style="left:263px">30.2888</div><div class="cell" style="left:341px">2.01574</div>
    <div class="cell" style="left:410px">23.305</div><div class="cell" style="left:478px">-0.149368</div>
    <div class="cell" style="left:552px">22.3054</div><div class="cell" style="left:624px">4.63714</div>
    <div class="cell" style="left:696px">0.945706</div><div class="cell" style="left:766px">2.81949</div>
    <div class="cell" style="left:833px">2.60858</div>
  </div>
  <div class="row">
    <svg class="star" viewBox="0 0 10 10"><path d="M5 .8 6.2 3.7H9.3L6.8 5.6 7.7 8.8 5 7 2.3 8.8 3.2 5.6.7 3.7H3.8Z"/></svg>
    <div class="cell" style="left:25px">Model 6</div><div class="cell" style="left:92px">Materials</div>
    <div class="cell" style="left:175px">2019-07-03<br>12:15:00.000</div>
    <div class="cell" style="left:263px">30.2888</div><div class="cell" style="left:341px">2.01574</div>
    <div class="cell" style="left:410px">23.305</div><div class="cell" style="left:478px">-0.149368</div>
    <div class="cell" style="left:552px">22.3054</div><div class="cell" style="left:624px">4.63714</div>
    <div class="cell" style="left:696px">0.945706</div><div class="cell" style="left:766px">2.81949</div>
    <div class="cell" style="left:833px">2.60858</div>
  </div>
</section>
</body>
</html>
```